BFCM Creatives Theme

We are looking for an initial design for our BFCM campaign this year to set the theme for all other creatives for BFCM. We are an ecommerce brand selling Merino wool baby clothing. Our flagship product is the Marlow Toddler Hush Pod (see images).

We are starting with the request for an instagram post, announcing the sale (details below). This post should be 1080x1350 but also look appealing in the square grid. I've attached a basic brand card showing color palette, fonts, and logos. I will also attach some image options. We are looking for your creativity to shine while aligning with our branding and connecting with the customer. If you have a specific idea and are looking for a specific image please contact us.

Sale Details:
- 20% Off Sitewide
- 11.28.24 - 12.02.24
- Excluding giftcards and imperfects. No rainchecks.

```html
<!DOCTYPE html>
<html lang="en">
<head>
<meta charset="utf-8">
<title>Fleecewell — 20% Off Sitewide</title>
<link rel="stylesheet" href="https://fonts.googleapis.com/css2?family=Fredoka:wght@500;600&family=Quicksand:wght@700&family=Sniglet&display=swap">
<style>
  :root {
    --ink: #35383a;
    --gold: #c6a54b;
    --gold-light: #e6d6a6;
    --slate: #76808c;
    --slate-light: #c9ced4;
    --paper: #ffffff;
  }
  html, body { margin: 0; padding: 0; overflow: hidden; background: var(--paper); }
  .poster {
    position: relative;
    width: 960px;
    height: 1200px;
    overflow: hidden;
    background: var(--paper);
    font-family: "Fredoka", sans-serif;
    color: var(--ink);
  }
  .corner-bands { position: absolute; inset: 0; width: 960px; height: 1200px; }
  .brand {
    position: absolute;
    top: 128px;
    left: 0;
    width: 960px;
    display: flex;
    justify-content: center;
    align-items: center;
    gap: 12px;
  }
  .brand-dot {
    width: 34px; height: 34px;
    border-radius: 50%;
    border: 2px solid var(--ink);
    box-sizing: border-box;
  }
  .brand-name {
    font-family: "Fredoka", sans-serif;
    font-weight: 500;
    font-size: 46px;
    line-height: 1;
    color: var(--ink);
  }
  .headline { position: absolute; left: 0; top: 205px; width: 960px; height: 190px; }
  .headline text {
    font-family: "Fredoka", sans-serif;
    font-weight: 600;
    font-size: 222px;
  }
  .sitewide {
    position: absolute;
    top: 392px;
    left: 0;
    width: 960px;
    text-align: center;
    font-family: "Quicksand", sans-serif;
    font-weight: 700;
    font-size: 144px;
    letter-spacing: 4px;
    line-height: 1;
    color: var(--gold);
    padding-left: 30px;
    box-sizing: border-box;
  }
  .photo {
    position: absolute;
    width: 169px;
    height: 133px;
    border: 2px solid var(--gold);
    border-radius: 10px;
    box-sizing: border-box;
  }
  .photo.stack { background: linear-gradient(160deg, #d8cbb6, #b49f84); }
  .photo.blue-crib { background: linear-gradient(90deg, #e7e8ea 20%, #6f97c8 50%, #e7e8ea 80%); }
  .photo.beige-sit { background: linear-gradient(180deg, #f1efec, #ddd2c2); }
  .photo.green-crib { background: linear-gradient(160deg, #f4f4f2, #b7c7a3 70%, #eef0ea); }
  .photo.pink-flat { background: linear-gradient(160deg, #efe9e3, #f2c4c4 55%, #ebe5de); }
  .photo.pink-crib { background: linear-gradient(90deg, #9ea1a3 15%, #f1d2d1 50%, #eceae8 85%); }
  .photo.stripe-crib { background: linear-gradient(90deg, #9fa2a4 15%, #e5eadf 50%, #f2f2f2 85%); }
  .photo.blue-peek { background: linear-gradient(180deg, #f6f6f6, #8eaed3 60%, #eeeeee); }
  .dates {
    position: absolute;
    top: 834px;
    left: 82px;
    font-family: "Fredoka", sans-serif;
    font-weight: 500;
    font-size: 100px;
    line-height: 1;
    letter-spacing: -1px;
    color: var(--ink);
    white-space: nowrap;
  }
  .exclusions {
    position: absolute;
    top: 942px;
    left: 85px;
    width: 706px;
    height: 55px;
    border-radius: 12px;
    background: var(--ink);
    color: var(--paper);
    font-family: "Sniglet", sans-serif;
    font-size: 38px;
    line-height: 55px;
    text-align: center;
    letter-spacing: 1px;
  }
  .rainchecks {
    position: absolute;
    top: 1012px;
    left: 0;
    width: 876px;
    text-align: center;
    font-family: "Sniglet", sans-serif;
    font-size: 44px;
    letter-spacing: 1px;
    line-height: 1;
    color: var(--ink);
  }
</style>
</head>
<body>
<main class="poster">
  <svg class="corner-bands" viewBox="0 0 960 1200" aria-hidden="true">
    <defs>
      <linearGradient id="slate-band" x1="0" y1="0" x2="1" y2="0">
        <stop offset="0" stop-color="#ffffff"/>
        <stop offset="0.35" stop-color="var(--slate-light)"/>
        <stop offset="1" stop-color="var(--slate)"/>
      </linearGradient>
      <linearGradient id="gold-band" x1="0" y1="0" x2="1" y2="0">
        <stop offset="0" stop-color="#ffffff"/>
        <stop offset="0.4" stop-color="var(--gold-light)"/>
        <stop offset="0.75" stop-color="var(--gold)"/>
      </linearGradient>
    </defs>
    <polygon points="40,0 960,0 929,166" fill="url(#slate-band)"/>
    <polygon points="360,0 960,0 960,164 940,162" fill="#ffffff"/>
    <polygon points="380,0 960,0 960,164" fill="url(#gold-band)"/>
    <polygon points="40,1200 929,1034 960,1034 960,1200" fill="url(#slate-band)"/>
    <polygon points="380,1200 960,1050 960,1200" fill="#ffffff"/>
    <polygon points="400,1200 960,1060 960,1200" fill="url(#gold-band)"/>
  </svg>

  <header class="brand">
    <span class="brand-dot"></span>
    <span class="brand-name">fleecewell</span>
  </header>

  <svg class="headline" viewBox="0 0 960 190" role="img" aria-label="20% OFF">
    <g text-anchor="start">
      <text x="84" y="175" textLength="790" lengthAdjust="spacingAndGlyphs" fill="none" stroke="var(--ink)" stroke-width="18" stroke-linejoin="round">20%OFF</text>
      <text x="84" y="175" textLength="790" lengthAdjust="spacingAndGlyphs" fill="none" stroke="var(--paper)" stroke-width="15" stroke-linejoin="round">20%OFF</text>
      <text x="84" y="175" textLength="790" lengthAdjust="spacingAndGlyphs" fill="var(--ink)">20%OFF</text>
    </g>
  </svg>

  <h1 class="sitewide" style="margin:0">SITEWIDE</h1>

  <div class="photo stack" style="left:154px;top:543px" role="img" aria-label="Stack of folded printed sleep sacks on a wooden stool"></div>
  <div class="photo blue-crib" style="left:339px;top:543px" role="img" aria-label="Baby in a blue printed sleep sack lying in a crib"></div>
  <div class="photo beige-sit" style="left:522px;top:543px" role="img" aria-label="Baby in a beige sleep sack sitting on a rug"></div>
  <div class="photo green-crib" style="left:707px;top:543px" role="img" aria-label="Baby in a sage green sleep sack sitting in a crib"></div>
  <div class="photo pink-flat" style="left:117px;top:693px" role="img" aria-label="Pink strawberry print sleep sack laid flat with accessories"></div>
  <div class="photo pink-crib" style="left:302px;top:693px" role="img" aria-label="Baby in a pink strawberry sleep sack lying in a crib"></div>
  <div class="photo stripe-crib" style="left:485px;top:693px" role="img" aria-label="Baby in a pale striped sleep sack lying in a crib"></div>
  <div class="photo blue-peek" style="left:669px;top:693px" role="img" aria-label="Baby in a blue sleep sack peeking through crib bars"></div>

  <p class="dates" style="margin:0">11.28.24–12.02.24</p>
  <p class="exclusions" style="margin:0">Excluding giftcards and imperfects.</p>
  <p class="rainchecks" style="margin:0">No rainchecks.</p>
</main>
</body>
</html>
```